Mira Ellsworth ADHD coach needs a flyer

I need a flyer to be sent by email. the copy is attached. It can be changed/reduced to fit the flyer. I would like to keep my website colors. My website is www.miraellsworth.net - Thank you!

```html
<!DOCTYPE html>
<html lang="en">
<head>
<meta charset="utf-8">
<title>Mira Ellsworth – Academic Coaching Flyer</title>
<link rel="stylesheet" href="https://fonts.googleapis.com/css2?family=Oswald:wght@500;700&family=Pathway+Gothic+One&family=Raleway:wght@700;800&family=Roboto+Condensed:wght@300;400;700&display=swap">
<style>
  :root{
    --backdrop:#3e4043;
    --mist:#cbd8dd;
    --mist-light:#dfe8eb;
    --steel:#8fb1bf;
    --slate:#5b7580;
    --ring:#56707a;
    --ink:#363636;
    --text:#3a3a3a;
    --panel:#ececec;
    --white:#ffffff;
    --quote:#d4d8da;
  }
  *{box-sizing:border-box;margin:0;padding:0}
  html,body{width:1200px;height:900px;overflow:hidden;background:var(--backdrop)}
  body{position:relative;font-family:'Roboto Condensed',sans-serif;color:var(--text)}

  .page{position:absolute;top:40px;width:580px;height:820px;background:var(--white);overflow:hidden}
  .page--front{left:12px}
  .page--back{left:608px}

  .abs{position:absolute}
  .name{font-family:'Pathway Gothic One',sans-serif;color:var(--slate);letter-spacing:.5px;line-height:1}

  /* ---------- front ---------- */
  .front-backdrop{left:0;top:0;z-index:0}
  .portrait{left:323px;top:0;width:257px;height:330px;z-index:1;
    background:linear-gradient(180deg,rgba(203,216,221,0) 0%,#d9cfd2 45%,#efe6e8 100%)}
  .front-name{left:23px;top:26px;font-size:40px;z-index:2}
  .headline{left:22px;top:70px;z-index:2;font-family:'Oswald',sans-serif;font-weight:700;font-size:44px;
    color:var(--white);letter-spacing:1px;line-height:1;text-shadow:0 2px 3px rgba(0,0,0,.45)}
  .subhead{left:24px;top:122px;width:340px;z-index:2;font-family:'Raleway',sans-serif;font-weight:700;
    font-size:13.2px;line-height:16.5px;color:var(--slate);letter-spacing:.2px}
  .intro-box{left:25px;top:160px;width:284px;height:180px;z-index:2;background:var(--steel);
    border-radius:10px 10px 0 0;padding:10px 12px 0;color:var(--white);text-align:center;
    font-size:9.4px;line-height:13.5px}
  .intro-box p + p{margin-top:7px}
  .swoosh{left:0;top:290px;z-index:3}

  .focus-ring{left:336px;top:236px;width:188px;height:188px;border-radius:50%;z-index:5;
    border:7px solid var(--ring);box-shadow:0 0 0 4px var(--white),0 4px 10px rgba(0,0,0,.25);
    background:linear-gradient(180deg,#6f7d45 0%,#9aa468 30%,#3d6e8f 62%,#1f4f70 100%);overflow:hidden}
  .focus-title{position:absolute;left:0;right:0;top:50px;text-align:center;color:var(--white);
    font-family:'Raleway',sans-serif;font-weight:800;font-size:11.5px;line-height:16px;text-shadow:0 1px 2px rgba(0,0,0,.5)}

  .results-box{left:309px;top:338px;width:246px;height:165px;z-index:4;background:var(--steel);
    border-radius:0 0 10px 10px;padding:96px 8px 0;text-align:center;color:var(--white);
    font-weight:700;font-size:10px;line-height:14px}

  .story{left:24px;top:351px;width:272px;z-index:3;font-size:9.5px;line-height:13.6px;text-align:justify}

  .potential{left:0;top:540px;width:309px;height:89px;background:var(--ink);padding:13px 24px 0;
    font-family:'Raleway',sans-serif;font-weight:800}
  .potential .kicker{color:var(--white);font-size:13.5px;line-height:18px}
  .potential .lead{color:var(--steel);font-size:14.5px;line-height:19px;margin-top:7px}

  .ticks{list-style:none}
  .ticks li{position:relative;padding-left:17px}
  .ticks li::before{content:"";position:absolute;left:0;top:2px;width:9px;height:9px;border:1px solid var(--slate);border-radius:50%}
  .ticks li::after{content:"";position:absolute;left:3.5px;top:4px;width:2.5px;height:4px;border:solid var(--slate);border-width:0 1px 1px 0;transform:rotate(45deg)}

  .change-list{left:24px;top:644px;width:280px;font-size:10px}
  .change-list li{height:21.8px}

  .guide-panel{left:309px;top:503px;width:246px;height:245px;border-radius:0 0 10px 10px;
    background:linear-gradient(180deg,#f2f2f2 0%,var(--panel) 100%);padding:14px 12px 0 12px;font-size:9.2px;line-height:12.8px}
  .guide-panel .lede{margin-bottom:9px}
  .guide-panel li{margin-bottom:4px}

  /* footer */
  .footer{left:0;top:776px;width:580px;height:44px;background:var(--steel)}
  .footer-band{position:absolute;left:0;top:0}
  .footer-text{position:absolute;left:0;right:0;top:6px;text-align:center;font-family:'Raleway',sans-serif;font-weight:800}
  .footer-text .cta{color:var(--steel);font-size:13.2px;line-height:16px;letter-spacing:.2px}
  .footer-text .contact{color:var(--white);font-size:8.6px;line-height:13px;margin-top:1px}

  /* ---------- back ---------- */
  .back-header{left:0;top:0;width:580px;height:74px;background:var(--mist)}
  .back-name{left:0;right:0;top:20px;text-align:center;font-size:40px}
  .tab{left:163px;top:74px;z-index:2}
  .tab-label{left:163px;top:74px;width:254px;height:32px;z-index:3;text-align:center;color:var(--white);
    font-family:'Raleway',sans-serif;font-weight:800;font-size:15px;line-height:32px}
  .benefits{top:118px;font-size:10px}
  .benefits li{height:22px}
  .benefits--left{left:24px;width:270px}
  .benefits--right{left:309px;width:260px}

  .section-title{left:0;width:580px;display:flex;align-items:center;justify-content:center;gap:20px;
    font-family:'Raleway',sans-serif;font-weight:800;font-size:18.5px;color:var(--steel)}
  .section-title::before,.section-title::after{content:"";width:56px;height:3px;background:var(--steel)}
  .section-title--top{top:174px}
  .section-title--band{top:468px;color:var(--white)}
  .section-title--band::before,.section-title--band::after{background:var(--white)}

  .photo{top:208px;height:153px;width:284px}
  .photo--a{left:0;background:linear-gradient(135deg,#8fb7d8 0%,#dbc2ae 55%,#a9c6e0 100%)}
  .photo--b{left:296px;background:linear-gradient(135deg,#d8d4cf 0%,#6e6a66 50%,#b29c8c 100%)}

  .quote{width:260px;text-align:center;font-size:10px;line-height:14px}
  .quote .by{margin-top:7px}
  .mark{font-family:'Oswald',sans-serif;font-weight:700;font-size:72px;line-height:1;color:var(--quote);z-index:0}
  .quote{z-index:1}
  .quote--a{left:12px;top:371px}
  .quote--b{left:308px;top:371px}

  .testimonial-band{left:0;top:458px;width:580px;height:302px;background:var(--steel)}
  .photo--c,.photo--d{top:501px;height:151px;width:284px;border:2px solid var(--white)}
  .photo--c{left:0;background:linear-gradient(160deg,#4f5e3a 0%,#a5a878 50%,#d9dccd 100%)}
  .photo--d{left:296px;background:linear-gradient(160deg,#7d6f5f 0%,#c6a489 45%,#6f74b0 100%)}
  .band-quote{color:var(--white)}
  .band-mark{color:rgba(255,255,255,.35)}
  .quote--c{left:12px;top:668px}
  .quote--d{left:308px;top:668px;font-size:9.6px;line-height:12.8px}
</style>
</head>
<body>

<!-- ===================== FRONT ===================== -->
<section class="page page--front" aria-label="Flyer front">
  <svg class="abs front-backdrop" width="580" height="360" viewBox="0 0 580 360" aria-hidden="true">
    <defs>
      <linearGradient id="mistFade" x1="0" y1="0" x2="0" y2="1">
        <stop offset="0" stop-color="#c7d5da"/>
        <stop offset="1" stop-color="#dbe5e8"/>
      </linearGradient>
    </defs>
    <rect width="580" height="360" fill="url(#mistFade)"/>
  </svg>

  <div class="abs portrait" role="img" aria-label="Portrait photo of the coach, smiling, in a light blazer with arms crossed"></div>

  <div class="abs name front-name">MIRA ELLSWORTH</div>
  <h1 class="abs headline">HELPING YOUR CHILD</h1>
  <p class="abs subhead">ADHD OR OTHER LEARNING CHALLENGES THRIVE IN COLLEGE AND BEYOND</p>

  <div class="abs intro-box">
    <p>Academic success coaching that leads to lifelong transformation for students with ADHD &amp; similar challenges that may have impeded their ability to thrive.</p>
    <p>Sending your child off to college can feel scary, especially if that college is hundreds of miles away. You worry about how they’ll do on their own—whether they’ll make friends, earn good grades, &amp; be happy—especially without you there to support them daily. You know your child is bright, &amp; you want them to have a great future, but you’re concerned they will struggle without the right support &amp; resources.</p>
  </div>

  <svg class="abs swoosh" width="580" height="75" viewBox="0 290 580 75" aria-hidden="true">
    <path d="M0 344 Q160 300 330 340 L580 326 V338 L330 352 Q160 318 0 362 Z" fill="#363636"/>
    <path d="M0 362 Q160 318 330 352 L580 338 V365 H0 Z" fill="#ffffff"/>
  </svg>

  <div class="abs results-box">Mira has taken students from failing to a 3.0 GPA, and from a C student to the Dean’s List, in just one semester. It doesn’t take years to provide lasting results; all it takes is the right guide.</div>

  <div class="abs focus-ring" role="img" aria-label="Photo of an open book on a table, softly lit outdoors">
    <div class="focus-title">EMPOWERING FOCUS:<br>HOW MIRA HELPS</div>
  </div>

  <p class="abs story">You don’t need to feel helpless as you send your child off to this next stage of their lives. Mira is dedicated to making that transition easier for everyone. Mira Ellsworth has years of experience helping students thrive despite their challenges. She sees your child’s potential and helps them see it, too. She provides a safety net as they adjust to a new environment at college. Her services are comprehensive and adaptable, based on the requirements of each individual: helping with course selection and scheduling, time management, study strategies, focus, making new friends, and adapting to change. Through it all, Mira guides students through fundamental work on mindset to ensure that changes stick.</p>

  <div class="abs potential">
    <div class="kicker">REALIZING POTENTIAL:</div>
    <div class="lead">THE TRANSFORMATION YOU’LL SEE IN YOUR CHILD</div>
  </div>

  <ul class="abs ticks change-list">
    <li>A mindset of self-belief and increased confidence.</li>
    <li>Higher grades and the drive to graduate.</li>
    <li>Social integration and making friends.</li>
    <li>Happiness and fulfilment.</li>
    <li>A deep sense of personal achievement and pride.</li>
  </ul>

  <div class="abs guide-panel">
    <p class="lede">Uniquely positioned to help your child, Mira:</p>
    <ul class="ticks">
      <li>Tailors support so that your child improves focus and maximizes their potential in college and beyond.</li>
      <li>Understands your child’s unique needs - she sees the gifts that others often miss.</li>
      <li>Knows the academic landscape intimately, including the challenges faced by students with ADHD and other conditions.</li>
      <li>Helps with the logistics of scheduling in a way that most advisors can’t, enrolling students in the courses that best suit their learning style.</li>
      <li>Nurtures the brilliance in your bright child.</li>
      <li>Provides a balance between encouraging students and challenging them.</li>
    </ul>
  </div>

  <footer class="abs footer">
    <svg class="footer-band" width="580" height="44" viewBox="0 0 580 44" aria-hidden="true">
      <path d="M21 0 H562 L541 44 H42 Z" fill="#363636"/>
    </svg>
    <div class="footer-text">
      <div class="cta">TO LEARN MORE AND DISCUSS YOUR CHILD’S INDIVIDUAL NEEDS,</div>
      <div class="contact">CALL : 555•010•4821 &nbsp;|&nbsp; EMAIL : COACH@MIRAELLSWORTH.NET &nbsp;|&nbsp; WEBSITE : WWW.MIRAELLSWORTH.NET</div>
    </div>
  </footer>
</section>

<!-- ===================== BACK ===================== -->
<section class="page page--back" aria-label="Flyer back">
  <div class="abs back-header"></div>
  <div class="abs name back-name">MIRA ELLSWORTH</div>

  <svg class="abs tab" width="254" height="32" viewBox="0 0 254 32" aria-hidden="true">
    <path d="M0 0 H254 L231 32 H24 Z" fill="#5b7580"/>
  </svg>
  <div class="abs tab-label">YOU WILL HAVE</div>

  <ul class="abs ticks benefits benefits--left">
    <li>Less stress, knowing that your child is in good hands.</li>
    <li>Fewer sleepless nights worrying about your child.</li>
  </ul>
  <ul class="abs ticks benefits benefits--right">
    <li>Confidence that they are receiving the right support.</li>
    <li>Joy and pride at seeing them do well.</li>
  </ul>

  <h2 class="abs section-title section-title--top">WHAT PARENTS SAY</h2>

  <div class="abs photo photo--a" role="img" aria-label="Photo of a smiling family of four outdoors under a blue sky"></div>
  <div class="abs photo photo--b" role="img" aria-label="Photo of parents sitting at home with two young children"></div>

  <div class="abs mark" style="left:26px;top:362px">“</div>
  <div class="abs mark" style="left:222px;top:400px">”</div>
  <div class="abs quote quote--a">
    <p>Mira was the glue that kept our daughter in college… as our daughter’s Academic Coach, [she] gave our daughter the ability to finish strong by empowering her with the skills needed to be successful.</p>
    <p class="by">- Renata -</p>
  </div>

  <div class="abs mark" style="left:318px;top:362px">“</div>
  <div class="abs mark" style="left:512px;top:400px">”</div>
  <div class="abs quote quote--b">
    <p>Mira has always told my daughter not that she can succeed, but that she will succeed.</p>
    <p class="by">- Lorna -</p>
  </div>

  <div class="abs testimonial-band"></div>
  <h2 class="abs section-title section-title--band">WHAT PARENTS SAY</h2>

  <div class="abs photo photo--c" role="img" aria-label="Photo of a schoolgirl in glasses holding a notebook in a grassy field"></div>
  <div class="abs photo photo--d" role="img" aria-label="Photo of a young girl writing in a notebook with a pen"></div>

  <div class="abs mark band-mark" style="left:24px;top:660px">“</div>
  <div class="abs mark band-mark" style="left:222px;top:696px">”</div>
  <div class="abs quote quote--c band-quote">
    <p>Last semester I completed all 16 hours and I had the highest GPA I’ve ever had!</p>
    <p class="by">- Former student -</p>
  </div>

  <div class="abs mark band-mark" style="left:314px;top:660px">“</div>
  <div class="abs mark band-mark" style="left:512px;top:696px">”</div>
  <div class="abs quote quote--d band-quote">
    <p>Under her instruction, my grades began to improve. I ended up making the Dean’s List during my time at Halden, and I was also inducted into Theta Lambda Nu. I am currently in my first year of law school at Westbrook University, a top tier school</p>
    <p class="by">- Former student -</p>
  </div>

  <footer class="abs footer">
    <svg class="footer-band" width="580" height="44" viewBox="0 0 580 44" aria-hidden="true">
      <path d="M21 0 H562 L541 44 H42 Z" fill="#363636"/>
    </svg>
    <div class="footer-text">
      <div class="cta">TO LEARN MORE AND DISCUSS YOUR CHILD’S INDIVIDUAL NEEDS,</div>
      <div class="contact">CALL : 555•010•4821 &nbsp;|&nbsp; EMAIL : COACH@MIRAELLSWORTH.NET &nbsp;|&nbsp; WEBSITE : WWW.MIRAELLSWORTH.NET</div>
    </div>
  </footer>
</section>

</body>
</html>
```